Corbell Lending Partners - Real estate loans - need a business card with a logo

I need a logo and a business card that looks elegant - that looks as if it is a big stablish corporation - We do real estate loans, my goal is to brand myself with colors black background - gold or silver letters - some combination - Name of the company different color than the rest of the card -

```html
<!DOCTYPE html>
<html lang="en">
<head>
<meta charset="utf-8">
<title>Corbell Lending Partners — Business Card</title>
<link rel="stylesheet" href="https://fonts.googleapis.com/css2?family=Montserrat:wght@400;500;600&display=swap">
<style>
  :root {
    --backdrop: #1e1e1f;
    --card: #0b0b0c;
    --card-edge: #151516;
    --gold: #c9a94e;
    --silver: #d6d6d8;
    --muted: #b9b9bc;
  }
  * { box-sizing: border-box; margin: 0; padding: 0; }
  html, body {
    width: 1200px; height: 890px; overflow: hidden;
    background: var(--backdrop);
    font-family: "Montserrat", Arial, sans-serif;
  }
  .stage {
    width: 1200px; height: 890px;
    display: flex; align-items: center; justify-content: center;
  }
  .card {
    position: relative;
    width: 910px; height: 520px;
    background: linear-gradient(135deg, var(--card) 0%, var(--card) 60%, var(--card-edge) 100%);
    border-radius: 34px;
    box-shadow: 0 24px 60px rgba(0,0,0,.55);
    display: flex; align-items: center;
    padding: 0 70px 0 110px;
  }
  .brand {
    width: 360px;
    display: flex; align-items: center;
  }
  .brand-name {
    color: var(--gold);
    font-weight: 600;
    font-size: 30px;
    line-height: 1.2;
    letter-spacing: .04em;
    text-transform: uppercase;
  }
  .divider {
    width: 3px; height: 210px;
    background: var(--gold);
    margin: 0 44px 0 30px;
  }
  .details { color: var(--silver); }
  .person-name {
    color: var(--gold);
    font-weight: 600; font-size: 25px;
    letter-spacing: .03em; text-transform: uppercase;
  }
  .person-title {
    font-weight: 600; font-size: 18px; margin-top: 4px;
  }
  .address {
    font-size: 17px; line-height: 1.4; margin: 24px 0 14px;
    color: var(--muted);
  }
  .contact-list { list-style: none; }
  .contact-item {
    display: flex; align-items: center; gap: 12px;
    font-size: 17px; line-height: 1.75; color: var(--muted);
  }
  .contact-icon { width: 20px; height: 20px; flex: none; }
  .contact-icon * { fill: var(--gold); }
</style>
</head>
<body>
<main class="stage">
  <section class="card" aria-label="Business card">
    <div class="brand">
      <span class="brand-name">Corbell Lending Partners</span>
    </div>
    <div class="divider" aria-hidden="true"></div>
    <div class="details">
      <h1 class="person-name">Marcus Whitfield</h1>
      <p class="person-title">Managing Director</p>
      <p class="address">145 Harbour Crest Road,<br>Oakvale, ON K2P 4R7</p>
      <ul class="contact-list">
        <li class="contact-item">
          <svg class="contact-icon" viewBox="0 0 24 24" aria-hidden="true"><path d="M3 8c0-2 2-4 9-4s9 2 9 4v2h-5V8H8v2H3zM6 11h12l2 9H4zM12 13a3 3 0 1 0 0 6 3 3 0 0 0 0-6z"/></svg>
          +15550142290
        </li>
        <li class="contact-item">
          <svg class="contact-icon" viewBox="0 0 24 24" aria-hidden="true"><path d="M2 5h20v14H2zM4 7l8 6 8-6v-.5H4z" fill-rule="evenodd"/></svg>
          mwhitfield@corbell.example
        </li>
        <li class="contact-item">
          <svg class="contact-icon" viewBox="0 0 24 24" aria-hidden="true"><path d="M12 2a10 10 0 1 0 0 20 10 10 0 0 0 0-20zm-1 4 3 1-1 3-3 1-2-2zm4 6 3 1-1 4-3 2-1-3z" fill-rule="evenodd"/></svg>
          www.corbell.example
        </li>
      </ul>
    </div>
  </section>
</main>
</body>
</html>
```